Brell Stone Company Business Cards

Front and Back Business Card - logo and text setup - cool design. I need workable photoshop or illustrator files so I can setup each employee card with design that is created
Updates

Hi everyone, thank you for the great entries. Please no more white and blue cards - there are so many already - black and silver only now please. thanks!

Target Market(s)

Construction Industry - Facility Managers

Industry/Entity Type

Construction

Contact Information for Business Card

I really like contemporary simplistic looks - clean neat....not opposed to seeing some black backrounds

Requirements
Must have
• Logo/website address with design on front only - www.brellstone-example.com (logo attached)
• Back:
• Name/Title/Company Address/Phone/email address
Nice to have
• Cool design
Should not have
• Nothing gimmicky like Fire or Water - since we are a Fire Protection company - it has all been done

```html
<!DOCTYPE html>
<html lang="en">
<head>
<meta charset="utf-8">
<title>Brell Stone Company – Business Cards</title>
<link href="https://fonts.googleapis.com/css2?family=Lato:wght@400;700;900&display=swap" rel="stylesheet">
<style>
  :root {
    --backdrop: #c4c4c4;
    --black: #161616;
    --silver: #b9bcc1;
    --silver-dark: #6f7379;
    --paper: #eceded;
    --grey-text: #6a6d72;
    --white: #ffffff;
  }
  * { box-sizing: border-box; margin: 0; padding: 0; }
  html, body {
    width: 1200px; height: 1200px; overflow: hidden;
    background: var(--backdrop);
    font-family: "Lato", sans-serif;
  }
  .stage { position: relative; width: 1200px; height: 1200px; }
  .card { position: absolute; left: 250px; width: 708px; height: 404px; }
  .card--front { top: 144px; background: var(--black); }
  .card--back { top: 582px; background: var(--paper); }

  .brand-name {
    font-weight: 900; letter-spacing: -1px; line-height: 1;
    display: flex; align-items: center; gap: 14px;
  }
  .brand-name__mark { display: inline-block; }

  .card--front .brand-name {
    position: absolute; left: 0; right: 0; top: 160px;
    justify-content: center; color: var(--white); font-size: 78px;
  }
  .card--front .brand-name__mark { width: 22px; height: 22px; background: var(--silver); }

  .front-site {
    position: absolute; left: 0; right: 0; top: 345px; text-align: center;
    color: var(--white); font-size: 21px;
  }
  .front-site .accent { color: var(--silver); }

  .card--back .brand-name {
    position: absolute; right: 41px; top: 62px;
    color: var(--black); font-size: 60px;
  }
  .card--back .brand-name__mark { width: 17px; height: 17px; background: var(--silver-dark); }

  .person { position: absolute; left: 38px; top: 222px; }
  .person__name { font-size: 22px; font-weight: 700; color: var(--black); }
  .person__name .accent { color: var(--silver-dark); }
  .person__title { font-size: 16px; color: var(--grey-text); margin-top: 2px; }

  .contact-list {
    position: absolute; left: 38px; top: 289px; list-style: none;
    font-size: 16px; color: var(--grey-text);
  }
  .contact-list li { display: flex; align-items: center; height: 21.3px; gap: 9px; }
  .icon { width: 12px; height: 12px; flex: none; }
  .icon__solid { fill: var(--silver-dark); }
  .icon__cut { fill: none; stroke: var(--paper); }
  .icon__tray { fill: var(--paper); stroke: var(--silver-dark); stroke-width: 1; }

  .address {
    position: absolute; right: 41px; top: 326px; text-align: right;
    font-size: 16px; line-height: 20px; color: var(--grey-text); font-style: normal;
  }
</style>
</head>
<body>
<main class="stage">
  <section class="card card--front" aria-label="Card front">
    <div class="brand-name"><span>Brell Stone</span><span class="brand-name__mark"></span></div>
    <p class="front-site">www.<span class="accent">brellstone-example</span>.com</p>
  </section>

  <section class="card card--back" aria-label="Card back">
    <div class="brand-name"><span>Brell Stone</span><span class="brand-name__mark"></span></div>

    <div class="person">
      <p class="person__name">Dana <span class="accent">Whitlock</span></p>
      <p class="person__title">Director</p>
    </div>

    <ul class="contact-list">
      <li>
        <svg class="icon" viewBox="0 0 12 12" aria-hidden="true"><path class="icon__solid" d="M2.4 0.6 4.3 2.8 3.3 4.2C4 5.8 5.6 7.6 7.6 8.6L8.9 7.6 11.2 9.5 10 11.4C5.3 11 0.9 6.4 0.6 1.9Z"/></svg>
        <span>(555) 014-2290</span>
      </li>
      <li>
        <svg class="icon" viewBox="0 0 12 12" aria-hidden="true"><rect class="icon__solid" x="3" y="0.5" width="6" height="3"/><rect class="icon__solid" x="0.5" y="4" width="11" height="5" rx="1"/><rect class="icon__tray" x="3" y="8" width="6" height="3.5"/></svg>
        <span>(555) 014-2291</span>
      </li>
      <li>
        <svg class="icon" viewBox="0 0 12 12" aria-hidden="true"><rect class="icon__solid" x="0.5" y="2" width="11" height="8"/><path class="icon__cut" stroke-width="1.2" d="M0.5 2 6 6.5 11.5 2"/></svg>
        <span>info@brellstone-example.com</span>
      </li>
      <li>
        <svg class="icon" viewBox="0 0 12 12" aria-hidden="true"><circle class="icon__solid" cx="6" cy="6" r="5.5"/><g class="icon__cut" stroke-width="0.9"><ellipse cx="6" cy="6" rx="2.3" ry="5.5"/><path d="M0.5 6H11.5M1.3 3.4H10.7M1.3 8.6H10.7"/></g></svg>
        <span>www.brellstone-example.com</span>
      </li>
    </ul>

    <address class="address">
      48 Harbor Works Lane<br>
      Millbrook, NY 10990
    </address>
  </section>
</main>
</body>
</html>
```